CREATE A BUSINESS CARD FOR A BOAT CLEANING SERVICE

WE ARE STARTING A NEW BOAT CLEANING BUSINESS. WE DIVE UNDERWATER TO CLEAN BOAT HULLS, JETTIES, UNDERWATER STRUCTURES ETC. WE ARE LOOKING FOR AN UPPERMARKET MODERN LOGO AND BUSINESS CARD AS ALOT OF OUR TARGET MARKET WILL BE HIGH END. YOU HAVE TO DESIGN A BUSINESS CARD AND LOGO SEPERATELY .
THE BUSINESS CARD DIMESNION MUST BE STANDARD SIZE.
The standard dimensions of a printed business card are 3.5 x 2 inches

Target Market(s)

UNDERWATER SERVICED

Industry/Entity Type

Business

Contact Information for Business Card

HOLLAND UNDERWATER SERVICES

Font styles to use
Serif

Colors

Designer to choose colors to be used in the design.

Requirements
Must have
• HOLLAND
Nice to have
• dark
Should not have
• more than 3 colors

```html
<!DOCTYPE html>
<html lang="en">
<head>
<meta charset="utf-8">
<title>Holland Underwater Service – Business Card</title>
<link rel="stylesheet" href="https://fonts.googleapis.com/css2?family=Lato:wght@400&family=Oswald:wght@500&display=swap">
<style>
  :root {
    --backdrop: #181818;
    --card-white: #ffffff;
    --brand-blue: #16518b;
    --ink: #1e2a36;
    --glow: #f3f4f6;
  }
  * { margin: 0; padding: 0; box-sizing: border-box; }
  html, body { width: 1200px; height: 897px; overflow: hidden; background: var(--backdrop); }
  .stage { position: relative; width: 1200px; height: 897px; }

  .card {
    position: absolute;
    left: 303px;
    width: 595px;
    height: 338px;
    border-radius: 20px;
    overflow: hidden;
  }
  .card--front { top: 92px; background: var(--card-white); }
  .card--back { top: 469px; background: var(--brand-blue); }

  .front-glow {
    position: absolute;
    left: 300px; top: -60px;
    width: 340px; height: 340px;
    border-radius: 50%;
    background: radial-gradient(circle, var(--glow) 0%, rgba(243,244,246,0.5) 45%, rgba(255,255,255,0) 72%);
  }

  .identity {
    position: absolute;
    right: 324px;
    top: 135px;
    text-align: right;
  }
  .identity__name {
    font-family: "Oswald", sans-serif;
    font-weight: 500;
    font-size: 33px;
    line-height: 1;
    color: var(--brand-blue);
    letter-spacing: 0.5px;
  }
  .identity__role {
    margin-top: 8px;
    font-family: "Lato", sans-serif;
    font-size: 17px;
    color: var(--ink);
  }

  .divider {
    position: absolute;
    left: 296px; top: 136px;
    width: 2px; height: 70px;
    background: var(--brand-blue);
  }

  .contacts {
    position: absolute;
    left: 325px; top: 131px;
    list-style: none;
  }
  .contacts li {
    display: flex;
    align-items: center;
    height: 19.3px;
    font-family: "Lato", sans-serif;
    font-size: 14.5px;
    color: var(--ink);
  }
  .contacts svg {
    width: 11px; height: 11px;
    margin-right: 11px;
    fill: var(--brand-blue);
  }

  .location {
    position: absolute;
    left: 103px; top: 296px;
    font-family: "Lato", sans-serif;
    font-size: 14px;
    color: var(--ink);
  }
  .location__label { color: var(--brand-blue); }

  .company-name {
    position: absolute;
    left: 0; right: 0;
    top: 178px;
    text-align: center;
    font-family: "Lato", sans-serif;
    font-weight: 400;
    font-size: 27px;
    line-height: 1.2;
    color: var(--card-white);
  }

  .back-url {
    position: absolute;
    left: 0; right: 0; top: 291px;
    text-align: center;
    font-family: "Lato", sans-serif;
    font-size: 16px;
    letter-spacing: 0.5px;
    color: var(--card-white);
  }
</style>
</head>
<body>
<main class="stage">
  <section class="card card--front" aria-label="Business card front">
    <div class="front-glow"></div>

    <div class="identity">
      <h1 class="identity__name">TOM VERHOEVEN</h1>
      <p class="identity__role">CEO / Founder</p>
    </div>

    <div class="divider"></div>

    <ul class="contacts">
      <li>
        <svg viewBox="0 0 24 24" aria-hidden="true"><path d="M6.6 10.8a15.1 15.1 0 0 0 6.6 6.6l2.2-2.2c.3-.3.7-.4 1-.2 1.1.4 2.3.6 3.6.6.6 0 1 .4 1 1V20c0 .6-.4 1-1 1A17 17 0 0 1 3 4c0-.6.4-1 1-1h3.5c.6 0 1 .4 1 1 0 1.3.2 2.5.6 3.6.1.3 0 .7-.2 1z"/></svg>
        212-555-0147
      </li>
      <li>
        <svg viewBox="0 0 24 24" aria-hidden="true"><path d="M2 8c0-2 4-4 10-4s10 2 10 4v2h-5V8H7v2H2zM6 11h12l3 9H3zm6 2a3 3 0 1 0 0 6 3 3 0 0 0 0-6z"/></svg>
        844-555-0199
      </li>
      <li>
        <svg viewBox="0 0 24 24" aria-hidden="true"><path d="M2 5h20v2l-10 6L2 7zm0 4.3l10 6 10-6V19H2z"/></svg>
        info@hollandunderwater.com
      </li>
      <li>
        <svg viewBox="0 0 24 24" aria-hidden="true"><path d="M12 2a10 10 0 1 0 0 20 10 10 0 0 0 0-20zm0 2c.9 0 2.2 1.8 2.7 5H9.3C9.8 5.8 11.1 4 12 4zm-2.9.6A12 12 0 0 0 7.3 9H4.6a8 8 0 0 1 4.5-4.4zm5.8 0A8 8 0 0 1 19.4 9h-2.7a12 12 0 0 0-1.8-4.4zM4.1 11h3a16 16 0 0 0 0 2h-3a8 8 0 0 1 0-2zm5 0h5.8a14 14 0 0 1 0 2H9.1a14 14 0 0 1 0-2zm7.8 0h3a8 8 0 0 1 0 2h-3a16 16 0 0 0 0-2zM4.6 15h2.7a12 12 0 0 0 1.8 4.4A8 8 0 0 1 4.6 15zm4.7 0h5.4c-.5 3.2-1.8 5-2.7 5s-2.2-1.8-2.7-5zm7.4 0h2.7a8 8 0 0 1-4.5 4.4 12 12 0 0 0 1.8-4.4z"/></svg>
        www.hollandunderwater.com
      </li>
    </ul>

    <p class="location"><span class="location__label">Location</span>: Havenkade 21 4811AB, Breda, The Netherlands</p>
  </section>

  <section class="card card--back" aria-label="Business card back">
    <p class="company-name">Holland Underwater Service</p>
    <p class="back-url">www.hollandunderwater.com</p>
  </section>
</main>
</body>
</html>
```